BUSINESS CARD FOR GUITAR SCHOOL

I would like to design a business card for my Guitar Music School. The school is called "Pluck & Lantern".

The card should be yellow.

Target Market(s)

18-35 years old

Industry/Entity Type

School

Contact Information for Business Card

I would like to design a business card for my Guitar Music School. The school is called "Pluck & Lantern". The card should be yellow.

Card must be consistent with my website design: www.pluckandlantern.com.sg

Requirements
Must have
• 1) Name of Company
• 2) Company Logo
• 3) Name of Employee
• 4) Position of Employee
• 5) Contact Number
• 6) Address
Nice to have
• Creative Design
• Card must be consistent with my website design: www.pluckandlantern.com.sg
Should not have
• Boring Design

```html
<!DOCTYPE html>
<html lang="en">
<head>
<meta charset="utf-8">
<title>Pluck &amp; Lantern – Business Card</title>
<link href="https://fonts.googleapis.com/css2?family=Lato:wght@400;700;900&family=Lora:ital@1&display=swap" rel="stylesheet">
<style>
  :root {
    --backdrop: #1c1c1c;
    --card-yellow: #f7b92a;
    --ink: #2b2b2b;
    --band: #2e2e2e;
    --band-text: #d9d9d9;
    --muted: #f3efe4;
  }
  * { box-sizing: border-box; margin: 0; padding: 0; }
  html, body { width: 1200px; height: 873px; overflow: hidden; }
  body {
    background: var(--backdrop);
    font-family: "Lato", sans-serif;
    position: relative;
  }
  .card {
    position: absolute;
    width: 520px;
    height: 300px;
    background: var(--card-yellow);
    overflow: hidden;
    box-shadow: 0 10px 30px rgba(0,0,0,.5);
  }
  .card--back { left: 70px; top: 140px; }
  .card--front { left: 610px; top: 430px; }

  .brand { text-align: center; color: var(--ink); }
  .brand__name {
    font-weight: 900;
    font-size: 50px;
    letter-spacing: -1px;
    line-height: 1;
  }
  .brand__tagline {
    font-weight: 400;
    font-size: 13px;
    margin-top: 6px;
  }
  .card--back .brand { position: absolute; left: 0; right: 0; top: 70px; }

  .back-band {
    position: absolute; left: 0; right: 0; bottom: 0; height: 84px;
    background: var(--band);
    color: var(--band-text);
    font-weight: 700;
    font-size: 15px;
    text-align: center;
    padding-top: 20px;
    line-height: 1.6;
  }
  .back-band .highlight { color: var(--card-yellow); }

  .card--front .brand { position: absolute; left: 70px; top: 36px; width: 320px; }
  .card--front .brand__name { font-size: 40px; }
  .card--front .brand__tagline { font-size: 11px; }

  .person { position: absolute; right: 34px; top: 112px; text-align: right; }
  .person__name { font-weight: 900; font-size: 20px; color: var(--ink); }
  .person__role { font-weight: 700; font-size: 13px; color: var(--muted); margin-top: 2px; }

  .contact {
    position: absolute; left: 28px; top: 140px;
    list-style: none;
    font-weight: 700; font-size: 13px; color: var(--ink);
  }
  .contact li { display: flex; align-items: flex-start; gap: 10px; margin-bottom: 6px; line-height: 1.3; }
  .contact svg { flex: none; width: 14px; height: 14px; margin-top: 1px; fill: var(--muted); }

  .front-band { position: absolute; left: 0; bottom: 0; width: 520px; height: 90px; }
  .front-band__cta {
    position: absolute; left: 28px; bottom: 11px;
    font-weight: 700; font-size: 15px; line-height: 18px; color: var(--band-text);
  }
  .front-band__motto {
    position: absolute; right: 18px; top: 227px;
    font-family: "Lora", serif; font-style: italic;
    font-size: 15px; line-height: 20px; color: var(--band-text);
    white-space: nowrap;
  }
</style>
</head>
<body>

<section class="card card--back" aria-label="Card back">
  <div class="brand">
    <div class="brand__name">Pluck &amp; Lantern</div>
    <div class="brand__tagline">Taking Worship to the Next Level</div>
  </div>
  <div class="back-band">
    Whether you are a budding beginner or an seasoned strummer..<br>
    We can take you to the <span class="highlight">next level..</span>
  </div>
</section>

<section class="card card--front" aria-label="Card front">
  <div class="brand">
    <div class="brand__name">Pluck &amp; Lantern</div>
    <div class="brand__tagline">Taking Worship to the Next Level</div>
  </div>

  <div class="person">
    <div class="person__name">Maya Tan</div>
    <div class="person__role">Owner / Founder</div>
  </div>

  <ul class="contact">
    <li>
      <svg viewBox="0 0 16 16" aria-hidden="true"><path d="M3 2h3l1 3-2 1c1 2 2 3 4 4l1-2 3 1v3c0 1-1 2-2 2C6 14 2 10 2 4c0-1 0-2 1-2z"/></svg>
      +65 9104 5826
    </li>
    <li>
      <svg viewBox="0 0 16 16" aria-hidden="true"><path d="M1 3h14v10H1z M2 4l6 5 6-5" stroke="#f7b92a" stroke-width="1"/></svg>
      Daniel@pluckandlantern.com.sg
    </li>
    <li>
      <svg viewBox="0 0 16 16" aria-hidden="true"><path d="M8 1a5 5 0 0 1 5 5c0 4-5 9-5 9S3 10 3 6a5 5 0 0 1 5-5zm0 3a2 2 0 1 0 0 4 2 2 0 0 0 0-4z"/></svg>
      22 Keppel Lane, Harbour Building,<br>B #05-03, Singapore
    </li>
  </ul>

  <svg class="front-band" viewBox="0 0 520 90" aria-hidden="true">
    <polygon points="0,50 520,50 520,90 0,90" fill="#2e2e2e"/>
    <polygon points="278,5 520,5 520,50 240,50" fill="#2e2e2e"/>
    <polygon points="222,50 260,5 266,5 228,50" fill="#2e2e2e"/>
  </svg>
  <div class="front-band__cta">JOIN OUR FREE TRIAL CLASS</div>
  <div class="front-band__motto">Ignite your passion for playing..</div>
</section>

</body>
</html>
```